High profile consulting company needs a Business Card Design

I need a business card design for a coaching /consulting company. We specialize in changing behaviors. Our services include therapy, workshops, life coaching, etc.

Check out our website to get a feel for our personality. www.oakbridgeadvisory.com

The new logo will be attached to the website soon, I have attached the new logo for your use on the business card.
Updates

I forgot to provide you with the company email under the "must have" section for the business card.  The website is:

 www.oakbridgeadvisory.com

I understand there's some trouble with the logo I uploaded.  I will try that again.  Thank you for your efforts.

Dana

Thank you for some of your questions.  I prefer a one sided business card, and tend to like the white backgrounds.

I also made 2 small changes to the content.  

add MFT after the name:  Dana Holloway, MFT

and the tag line needed more clarity once I saw it.  Please change it to:  Improving performance by strengthening relationships and changing behaviors.

Thank you,
Dana

Industry/Entity Type

Business

Requirements
Must have
• logo
Phone number: 415-207-5146
email: Dana@oakbridgeadvisory.com
Dana Holloway, MFT
President
Nice to have
• Improving performance by strengthening relationships and changing behaviors.

```html
<!DOCTYPE html>
<html lang="en">
<head>
<meta charset="utf-8">
<title>Oakbridge Advisory – Business Card</title>
<link rel="stylesheet" href="https://fonts.googleapis.com/css2?family=Jost:wght@400;500;600&display=swap">
<style>
  :root {
    --brand-green: #0b6a4f;
    --card-white: #f7f7f6;
    --ink-dark: #2d2d2d;
    --ink-grey: #6b6b6b;
    --mark-grey: #7a7a7a;
    --backdrop: #d9d9d9;
  }
  * { box-sizing: border-box; margin: 0; padding: 0; }
  html, body {
    width: 1200px; height: 900px; overflow: hidden;
    background: var(--backdrop);
    font-family: "Jost", "Futura", sans-serif;
  }
  .stage { position: relative; width: 1200px; height: 900px; }
  .card {
    position: absolute; width: 560px; height: 320px;
    box-shadow: 0 6px 18px rgba(0,0,0,0.18);
    overflow: hidden;
  }
  /* Front */
  .card-front {
    left: 140px; top: 110px;
    background: var(--brand-green);
    display: flex; flex-direction: column; align-items: center; justify-content: center;
    gap: 18px;
  }
  .front-mark {
    width: 84px; height: 84px; border-radius: 50%;
    background: #ffffff;
  }
  .front-name {
    color: #ffffff; font-weight: 600; font-size: 34px; letter-spacing: 1px;
    text-transform: uppercase;
  }
  /* Back */
  .card-back {
    left: 500px; top: 470px;
    background: var(--card-white);
  }
  .back-arc { position: absolute; left: 0; top: 0; }
  .back-brand {
    position: absolute; left: 38px; top: 104px; width: 150px;
    display: flex; flex-direction: column; align-items: center; gap: 10px;
  }
  .back-mark {
    width: 82px; height: 82px; border-radius: 50%; background: var(--mark-grey);
  }
  .back-brand-name {
    color: var(--mark-grey); font-size: 14px; font-weight: 500; text-align: center;
  }
  .details { position: absolute; left: 252px; top: 62px; width: 290px; }
  .person-name { color: var(--ink-dark); font-size: 21px; font-weight: 500; }
  .person-title { color: var(--ink-grey); font-size: 15px; margin-top: 2px; }
  .contact-list { list-style: none; margin-top: 30px; }
  .contact-item {
    display: flex; align-items: center; gap: 8px;
    color: var(--ink-grey); font-size: 14.5px; line-height: 22px;
  }
  .contact-icon { width: 13px; height: 13px; flex: none; }
  .tagline {
    margin-top: 34px; color: var(--ink-grey); font-size: 13.5px; line-height: 18px;
  }
</style>
</head>
<body>
<main class="stage">
  <section class="card card-front" aria-label="Card front">
    <div class="front-mark"></div>
    <div class="front-name">Oakbridge Advisory</div>
  </section>

  <section class="card card-back" aria-label="Card back">
    <svg class="back-arc" width="560" height="320" viewBox="0 0 560 320" aria-hidden="true">
      <circle cx="30" cy="160" r="195" fill="none" stroke="var(--brand-green)" stroke-width="15"/>
    </svg>
    <div class="back-brand">
      <div class="back-mark"></div>
      <div class="back-brand-name">Oakbridge Advisory</div>
    </div>
    <div class="details">
      <div class="person-name">Dana Holloway, MFT</div>
      <div class="person-title">President</div>
      <ul class="contact-list">
        <li class="contact-item">
          <svg class="contact-icon" viewBox="0 0 16 16" aria-hidden="true"><path fill="var(--brand-green)" d="M3 2h3l1.5 3.5-2 1.3a9 9 0 0 0 3.7 3.7l1.3-2L14 10v3a1.5 1.5 0 0 1-1.5 1.5A11.5 11.5 0 0 1 1.5 3.5 1.5 1.5 0 0 1 3 2z"/></svg>
          415-207-5146
        </li>
        <li class="contact-item">
          <svg class="contact-icon" viewBox="0 0 16 16" aria-hidden="true"><rect x="1" y="3" width="14" height="10" fill="var(--brand-green)"/><path d="M1.5 3.5 8 9l6.5-5.5" fill="none" stroke="#fff" stroke-width="1.3"/></svg>
          Dana@oakbridgeadvisory.com
        </li>
        <li class="contact-item">
          <svg class="contact-icon" viewBox="0 0 16 16" aria-hidden="true"><g fill="none" stroke="var(--brand-green)" stroke-width="1.4"><circle cx="8" cy="8" r="6.5"/><ellipse cx="8" cy="8" rx="2.8" ry="6.5"/><path d="M1.5 8h13"/></g></svg>
          www.oakbridgeadvisory.com
        </li>
      </ul>
      <p class="tagline">improving performance by strengthening<br>relationships and changing behaviors</p>
    </div>
  </section>
</main>
</body>
</html>
```